Thank You Card Design for Personal Injury Law Firm

Hi -
I am interested in getting a design for a thank you card that captures my law firm's brand. I am providing a drop box link to a folder that contains pictures of the firm's staff and some happy clients. The dropbox folder will also include a folder that we mail to prospective clients. You may want to use pictures from it in addition to or in place of staff and client pictures. https://www.filquorra.net/sh/pelv3kx7tumwq2b/ZTRNLbcHoWEqJFm42tixpRk8y?dl=0

Target Market(s)

Adult males and females who have been in car accidents

Industry/Entity Type

Legal

Requirements
Nice to have
• Want it to have a happy, cheerful feel. But it must also be professional.

```html
<!DOCTYPE html>
<html lang="en">
<head>
<meta charset="utf-8">
<title>Harlow Law Group – Thank You Card</title>
<link rel="stylesheet" href="https://fonts.googleapis.com/css2?family=Montserrat:wght@500;600;700;800&display=swap">
<style>
  :root {
    --brand-blue: #1d4f7c;
    --brand-blue-deep: #163f64;
    --ink-grey: #5a5f66;
    --card-white: #ffffff;
    --backdrop: #e9e6e1;
    --photo-suit: #3f5f86;
    --photo-skin: #d9b59a;
    --photo-office: #c9cdd3;
    --photo-garden: #6f8f4e;
    --photo-warm: #9a5a44;
    --photo-sky: #b9c9d8;
  }
  * { box-sizing: border-box; margin: 0; padding: 0; }
  html, body { width: 1200px; height: 800px; overflow: hidden; }
  body {
    background: var(--backdrop);
    font-family: "Montserrat", Arial, sans-serif;
    display: flex; align-items: center; justify-content: center;
  }
  .card {
    position: relative;
    width: 1040px; height: 740px;
    background: var(--card-white);
    box-shadow: 0 6px 24px rgba(0,0,0,0.12);
    overflow: hidden;
  }
  /* Brand block */
  .brand {
    position: absolute; left: 76px; top: 112px;
    display: flex; align-items: center; gap: 16px;
  }
  .brand-square { width: 84px; height: 78px; background: var(--brand-blue); }
  .brand-name {
    color: var(--brand-blue);
    font-weight: 600; font-size: 30px; line-height: 1.1;
    letter-spacing: 0.04em; text-transform: uppercase;
  }
  /* Greeting */
  .greeting {
    position: absolute; left: 86px; top: 300px;
    color: var(--brand-blue); font-weight: 800; line-height: 0.9;
  }
  .greeting-first { display: block; font-size: 66px; letter-spacing: -0.01em; }
  .greeting-second { display: block; font-size: 118px; margin-left: 118px; letter-spacing: -0.02em; }
  /* Contact */
  .contact {
    position: absolute; left: 60px; width: 360px; top: 600px;
    text-align: center; color: var(--brand-blue);
  }
  .contact-phone { font-size: 30px; font-weight: 700; letter-spacing: 0.04em; }
  .contact-address { font-size: 16px; font-weight: 600; margin-top: 8px; }
  .contact-web { font-size: 16px; font-weight: 600; margin-top: 6px; }
  /* Photo mosaics */
  .rule-vertical { position: absolute; left: 470px; width: 5px; background: var(--brand-blue); }
  .rule-vertical.top { top: 0; height: 326px; }
  .rule-vertical.bottom { top: 420px; height: 320px; }
  .mosaic {
    position: absolute; left: 484px; right: 26px;
    display: grid; gap: 5px;
    grid-template-columns: 1.1fr 1fr 1fr;
    grid-template-rows: 1fr 1fr;
  }
  .mosaic.top { top: 0; height: 300px; }
  .mosaic.bottom { top: 440px; height: 300px; }
  .rule-horizontal { position: absolute; left: 470px; right: 26px; height: 5px; background: var(--brand-blue); }
  .rule-horizontal.top { top: 310px; }
  .rule-horizontal.bottom { top: 424px; }
  .photo { width: 100%; height: 100%; }
  .photo.suit { background: linear-gradient(160deg, var(--photo-office), var(--photo-suit)); }
  .photo.office { background: linear-gradient(180deg, var(--photo-sky), var(--photo-office)); }
  .photo.warm { background: linear-gradient(170deg, var(--photo-skin), var(--photo-warm)); }
  .photo.garden { background: linear-gradient(180deg, #9fb57e, var(--photo-garden)); }
  .photo.blue { background: linear-gradient(170deg, var(--photo-sky), var(--brand-blue-deep)); }
</style>
</head>
<body>
  <main class="card">
    <div class="brand">
      <div class="brand-square"></div>
      <div class="brand-name">Harlow<br>Law Group</div>
    </div>

    <h1 class="greeting">
      <span class="greeting-first">Thank</span>
      <span class="greeting-second">You</span>
    </h1>

    <address class="contact">
      <div class="contact-phone">555 014 2870</div>
      <div class="contact-address">214 Birch Street • Northfield, AK 99590</div>
      <div class="contact-web">www.harlowlawgroup.example</div>
    </address>

    <div class="rule-vertical top"></div>
    <section class="mosaic top" aria-label="Firm staff photographs">
      <div class="photo suit" role="img" aria-label="Attorney in a suit seated at his desk"></div>
      <div class="photo office" role="img" aria-label="Two attorneys standing in front of the office sign"></div>
      <div class="photo warm" role="img" aria-label="Smiling staff member outside the office"></div>
      <div class="photo blue" role="img" aria-label="Staff members holding a newborn baby"></div>
      <div class="photo warm" role="img" aria-label="Attorney in a vest seated at a desk"></div>
      <div class="photo garden" role="img" aria-label="Two staff members standing among greenery"></div>
    </section>
    <div class="rule-horizontal top"></div>

    <div class="rule-horizontal bottom"></div>
    <div class="rule-vertical bottom"></div>
    <section class="mosaic bottom" aria-label="Happy client photographs">
      <div class="photo warm" role="img" aria-label="Smiling client seated on a red sofa"></div>
      <div class="photo blue" role="img" aria-label="Client in a blue shirt seated at a table"></div>
      <div class="photo garden" role="img" aria-label="Smiling client outdoors among trees"></div>
      <div class="photo garden" role="img" aria-label="Attorney shaking hands with a client in a garden"></div>
      <div class="photo office" role="img" aria-label="Laughing client leaning on a railing"></div>
      <div class="photo garden" role="img" aria-label="Couple walking together outdoors"></div>
    </section>
  </main>
</body>
</html>
```